Need a Wordpress website for my HVAC company

I need a Wordpress website created for an HVAC company in a competitive market.
Following are some websites I like:
My current website is www.borvicoheating.com - we also have a facebook page with some pictures

We are an airconditioning and heating company that does both residential and commmercial work.
We need the following info on our website:
-mobile friendly
-Schedule an appt -repair/maintnenace/installation (i would like this option to always be on the page even if they scroll down.)
-24 hour service
-coupons /promotions
-financing
-reviews/testimonials
-about
-blog
-Our service area
The following are services we provide:
-Air conditioning - Installation/Service/Maintenance/new construction
-Heating - Installation/Service/Maintenance/new construction ( gas furnace, 2 stage furnace, electric heat)
-Duct - Repair/Replacement/Istallation - (zone systems)
-thermostats (wifi)
-Heat pump
-Air handler
-self communicating systems
-carbon monoxide testing
-hail damage
-duct sealing
-insulation
-Air cleaners - UV Air purifiers
-humidifiers

I would also like Quilbo SEO add on

Target Market(s)

Anyone who needs our services HVAC contractor

Industry/Entity Type

Hvac

Contact Information for Business Card

Phone:480-555-2046
website:www.borvicoheating.com
email pmarsh@borvicoheating.com

Coding

Coded - Design and coding required

Number of Pages Required

5+ page

Font styles to use
Serif
Sans Serif

Requirements
Must have
• I wrote in brief. I already have Webly Nest. Long story I paid for 3 years already. I need someone to put website there. Ive never used Wordpress but would like a template page so I can easily add services.
Nice to have
• Clean, bright, original

```html
<!DOCTYPE html>
<html lang="en">
<head>
<meta charset="utf-8">
<title>Borvico Mechanical Services – Heating &amp; Cooling</title>
<link rel="stylesheet" href="https://fonts.googleapis.com/css2?family=Roboto+Condensed:wght@400;500;700&family=Roboto:wght@400;500&display=swap">
<style>
  :root {
    --blue: #1f7fcf;
    --blue-deep: #1b4f9a;
    --red: #d32a2e;
    --green: #2c9a44;
    --white: #ffffff;
    --ink: #1f2a36;
    --muted: #6a7480;
    --page: #f3f5f8;
    --card-red: rgba(211, 42, 46, 0.82);
    --card-green: rgba(44, 154, 68, 0.82);
    --card-blue: rgba(27, 79, 154, 0.85);
  }
  * { box-sizing: border-box; margin: 0; padding: 0; }
  html, body { width: 1200px; height: 676px; overflow: hidden; }
  body {
    position: relative;
    background: var(--page);
    font-family: "Roboto", Arial, sans-serif;
    color: var(--ink);
  }

  /* Top utility bar */
  .top-bar {
    position: absolute; left: 0; top: 0; width: 1200px; height: 40px;
    background: var(--white);
    display: flex; align-items: center; justify-content: flex-end;
    gap: 18px; padding-right: 50px;
    font-family: "Roboto Condensed", Arial, sans-serif;
  }
  .top-bar .phone { display: flex; align-items: center; gap: 5px; font-size: 14px; color: var(--muted); }
  .pill {
    font-size: 14px; font-weight: 500; color: var(--white);
    padding: 3px 7px; border-radius: 4px;
  }
  .pill.schedule { background: var(--red); }
  .pill.promo { background: var(--green); }
  .social { display: flex; gap: 14px; align-items: center; }
  .social .dot { width: 10px; height: 10px; border-radius: 50%; background: #9aa3ad; }

  /* Blue navigation band */
  .nav-band {
    position: absolute; left: 0; top: 40px; width: 1200px; height: 72px;
    background: var(--blue);
  }
  .main-nav {
    position: absolute; right: 50px; top: 0; height: 72px;
    display: flex; align-items: center; gap: 36px;
    font-family: "Roboto Condensed", Arial, sans-serif;
    font-weight: 500; font-size: 16px; color: var(--white);
    list-style: none;
  }

  /* Logo box */
  .brand-box {
    position: absolute; left: 55px; top: 0; width: 280px; height: 135px;
    background: var(--white);
    border-radius: 0 0 8px 8px;
    box-shadow: 0 3px 10px rgba(0,0,0,0.18);
    display: flex; align-items: center; justify-content: center; gap: 10px;
    padding: 0 18px;
  }
  .brand-box .mark { width: 16px; height: 16px; border-radius: 50%; background: var(--red); flex: none; }
  .brand-name {
    font-family: "Roboto Condensed", Arial, sans-serif;
    font-weight: 700; font-size: 22px; line-height: 1.1;
    color: var(--blue-deep); text-transform: uppercase;
  }

  /* Hero */
  .hero {
    position: absolute; left: 0; top: 112px; width: 1200px; height: 410px;
    background: linear-gradient(180deg, #8fb3d6 0%, #a99a84 38%, #7d7466 62%, #6f7a72 100%);
  }

  /* Service cards */
  .service-cards { position: absolute; left: 60px; top: 420px; width: 1080px; height: 180px; }
  .card { position: absolute; top: 0; width: 340px; }
  .card.repair { left: 0; }
  .card.maintenance { left: 370px; }
  .card.install { left: 740px; }
  .card-body {
    height: 110px; border-radius: 4px;
    padding: 48px 18px 0; text-align: center;
    font-size: 13px; line-height: 1.45; color: var(--white);
  }
  .repair .card-body { background: var(--card-red); }
  .maintenance .card-body { background: var(--card-green); }
  .install .card-body { background: var(--card-blue); }
  .card-icon {
    position: absolute; left: 50%; top: -44px; margin-left: -45px;
    width: 90px; height: 90px; border-radius: 50%;
    border: 3px solid var(--white);
    display: flex; align-items: center; justify-content: center;
  }
  .repair .card-icon { background: var(--red); }
  .maintenance .card-icon { background: var(--green); }
  .install .card-icon { background: var(--blue-deep); }
  .card-button {
    margin: -8px 16px 0; height: 50px; border-radius: 3px;
    display: flex; align-items: center; justify-content: center;
    font-family: "Roboto Condensed", Arial, sans-serif;
    font-weight: 500; font-size: 17px; color: var(--white); text-transform: uppercase;
    box-shadow: 0 3px 6px rgba(0,0,0,0.2);
  }
  .repair .card-button { background: var(--red); }
  .maintenance .card-button { background: var(--green); }
  .install .card-button { background: var(--blue-deep); }

  /* Our Services */
  .services-heading {
    position: absolute; left: 0; top: 606px; width: 1200px; text-align: center;
    font-family: "Roboto Condensed", Arial, sans-serif;
    font-weight: 700; font-size: 22px; color: var(--ink);
  }
  .services-heading span { color: var(--blue-deep); }
  .divider {
    position: absolute; left: 70px; top: 644px; width: 1060px;
    border-top: 1.5px dashed var(--blue);
  }
  .service-thumbs { position: absolute; left: 70px; top: 664px; width: 1060px; height: 12px; }
  .thumb { position: absolute; top: 0; width: 240px; height: 12px; }
  .thumb.t1 { left: 0; background: linear-gradient(90deg, #4a5a48, #d8d6cf); }
  .thumb.t2 { left: 272px; background: linear-gradient(90deg, #5f92c9, #8fb9e2); }
  .thumb.t3 { left: 544px; background: linear-gradient(90deg, #3e5fa8, #8aa6d4); }
  .thumb.t4 { left: 816px; background: var(--white); }
  .thumb-icon {
    position: absolute; top: -22px; width: 42px; height: 42px; border-radius: 50%;
    background: var(--blue-deep); border: 2px solid var(--white);
    display: flex; align-items: center; justify-content: center;
  }
  .t1 .thumb-icon { left: 100px; }
  .t2 .thumb-icon { left: 92px; }
  .t3 .thumb-icon { left: 96px; }
  .t4 .thumb-icon { left: 94px; }
</style>
</head>
<body>

  <header>
    <div class="top-bar">
      <span class="phone">
        <svg width="12" height="12" viewBox="0 0 24 24"><path d="M6.6 10.8a15 15 0 0 0 6.6 6.6l2.2-2.2a1 1 0 0 1 1-.25 11.4 11.4 0 0 0 3.6.6 1 1 0 0 1 1 1V20a1 1 0 0 1-1 1A17 17 0 0 1 3 4a1 1 0 0 1 1-1h3.5a1 1 0 0 1 1 1c0 1.25.2 2.45.6 3.6a1 1 0 0 1-.25 1z" fill="#6a7480"/></svg>
        +1 480-555-2046
      </span>
      <span class="pill schedule">Schedule Service</span>
      <span class="pill promo">Promotions Codes</span>
      <span class="social">
        <span class="dot"></span>
        <span class="dot"></span>
        <svg width="13" height="13" viewBox="0 0 24 24"><circle cx="10" cy="10" r="6.5" fill="none" stroke="#6a7480" stroke-width="3"/><path d="M15 15l6 6" stroke="#6a7480" stroke-width="3" stroke-linecap="round"/></svg>
      </span>
    </div>

    <div class="nav-band">
      <ul class="main-nav">
        <li>HOME</li>
        <li>ABOUT US</li>
        <li>OUR SERVICES</li>
        <li>BLOG</li>
        <li>TESTIMONIALS</li>
        <li>CONTACT US</li>
      </ul>
    </div>

    <div class="brand-box">
      <span class="mark"></span>
      <span class="brand-name">Borvico Mechanical Services</span>
    </div>
  </header>

  <main>
    <div class="hero" role="img" aria-label="Photo of company service vans parked in front of a suburban house with palm trees, beside a cartoon technician mascot"></div>

    <section class="service-cards">
      <article class="card repair">
        <div class="card-icon">
          <svg width="46" height="46" viewBox="0 0 48 48" fill="none" stroke="#fff" stroke-width="3" stroke-linecap="round">
            <path d="M10 38L30 18"/><circle cx="34" cy="13" r="6"/>
            <path d="M38 38L18 18"/><path d="M12 10l6 8"/><circle cx="40" cy="40" r="3"/>
          </svg>
        </div>
        <div class="card-body">Duis aute irure dolor in reprehenderit in voluptate velit esse cillum dolore eu fugiat nulla pariatur.</div>
        <div class="card-button">Repair</div>
      </article>

      <article class="card maintenance">
        <div class="card-icon">
          <svg width="40" height="44" viewBox="0 0 40 44" fill="none" stroke="#fff" stroke-width="3" stroke-linecap="round" stroke-linejoin="round">
            <rect x="6" y="6" width="28" height="34" rx="3"/><path d="M14 6V3h12v3"/>
            <path d="M12 17h10M12 25h10M12 33h8"/><path d="M26 16l2 2 3-4M26 24l2 2 3-4"/>
          </svg>
        </div>
        <div class="card-body">Duis aute irure dolor in reprehenderit in voluptate velit esse cillum dolore eu fugiat nulla pariatur.</div>
        <div class="card-button">Maintenace</div>
      </article>

      <article class="card install">
        <div class="card-icon">
          <svg width="44" height="44" viewBox="0 0 48 48" fill="none" stroke="#fff" stroke-width="3.5" stroke-linecap="round" stroke-linejoin="round">
            <path d="M10 20a15 15 0 0 1 27-6"/><path d="M38 6v9h-9"/>
            <path d="M38 28a15 15 0 0 1-27 6"/><path d="M10 42v-9h9"/>
          </svg>
        </div>
        <div class="card-body">Duis aute irure dolor in reprehenderit in voluptate velit esse cillum dolore eu fugiat nulla pariatur.</div>
        <div class="card-button">Installation</div>
      </article>
    </section>

    <section class="our-services">
      <h2 class="services-heading">Our <span>Services</span></h2>
      <div class="divider"></div>
      <div class="service-thumbs">
        <div class="thumb t1" role="img" aria-label="Photo of a residential home">
          <span class="thumb-icon"><svg width="22" height="22" viewBox="0 0 24 24" fill="none" stroke="#fff" stroke-width="2"><path d="M3 11l9-7 9 7"/><path d="M6 10v10h12V10"/><path d="M10 20v-5h4v5"/></svg></span>
        </div>
        <div class="thumb t2" role="img" aria-label="Photo of commercial buildings under blue sky">
          <span class="thumb-icon"><svg width="22" height="22" viewBox="0 0 24 24" fill="none" stroke="#fff" stroke-width="2"><rect x="4" y="8" width="16" height="13"/><path d="M8 8V4h8v4"/><path d="M8 12h2M14 12h2M8 16h2M14 16h2"/></svg></span>
        </div>
        <div class="thumb t3" role="img" aria-label="Photo of energy efficient equipment">
          <span class="thumb-icon"><svg width="22" height="22" viewBox="0 0 24 24" fill="none" stroke="#fff" stroke-width="2"><path d="M8 14a6 6 0 1 1 8 0v3H8z"/><path d="M9 20h6"/></svg></span>
        </div>
        <div class="thumb t4">
          <span class="thumb-icon"><svg width="22" height="22" viewBox="0 0 24 24" fill="none" stroke="#fff" stroke-width="2"><rect x="4" y="5" width="16" height="16" rx="2"/><path d="M4 10h16M8 3v4M16 3v4"/><path d="M10 13h4l-2 6"/></svg></span>
        </div>
      </div>
    </section>
  </main>

</body>
</html>
```